2 x Digitize Logo | 2 x Business Cards | 2 x Fridge Magnets

We require 6 deliverables:
1. Residential logo redrawn (same just high quality for large print format).
2. Corporate logo redrawn (minor changes to wording and high quality for large print format).
3. New business card design for Furniture Removals (residential)
4. New business card design for Corporate Relocations (business)
5. New Fridge magnet for Furniture removals (residential)
6. New fridge magnet for Corporate Relocations (business)
1. Residential Logo
a. We require the logo to be translated into a high quality digital image with no modifications.
(see attached resilogo.jpg)
2. Residential Logo
a. We require the logo to be edited (add the word corporate relocations) be translated into a high quality digital image.
(see attached corplogo.jpg)
3. Using the resilogo please make a new business card for our business.
a. Please see the web site https://www.larkbendcarters.com.au for colours and inspiration.
b. The residential business card needs the following information:
i. Business Name (using the residential logo).
ii. Free Call: 1800 LB Cart (the L, B and Cart much be the same colour as the logo).
iii. Website: www.LarkbendCarters.com.au
iv. Address: 4/17 Ormsdale Court, VIC 3264
v. Email: cart@LarkbendCarters.com.au
vi. backof Card:
Review our service
www.PennantOrbit.com.au
Services: Local, Country, Interstate | Furniture Removals | Piano, Billiard Tables & Antiques
4. Using the corplogo please make a new business card for our business.
b. The corporate business card needs the following information:
i. Business Name (using the corporate logo).
v. Email: corporate@LarkbendCarters.com.au
vi. Back of Card:
Review our service
www.PennantOrbit.com.au
Services: Corporate relocations | Office equipment moves | Packing Service | Packing Materials
5. Using the resilogo please make a new fridge magent for our business.
b. The residential fidge magnet needs the following information:
iv. Services: Local, Country, Interstate | Furniture Removals | Piano, Billiard Tables & Antiques
6. Using the corplogo please make a new fridge magent for our business.
b. The corporate fidge magnet needs the following information:
iv. Services: Local, Country, Interstate | Corporate relocations
Target Market(s)
Residential Furniture Removals and Corporate Office relocations
Industry/Entity Type
Business
Contact Information for Business Card
Please see full brief for six items required
Requirements
Must have
- Clean simple, easy to read
Nice to have
- fresh, stand out, eye catching
Should not have
- plain, standard, boring, general

```html
<!DOCTYPE html>
<html lang="en">
<head>
<meta charset="utf-8">
<title>Larkbend Carters – Business Cards</title>
<link rel="stylesheet" href="https://fonts.googleapis.com/css2?family=Open+Sans:wght@300;400;600;700&display=swap">
<style>
  :root {
    --backdrop: #626262;
    --card: #ffffff;
    --ink: #2b2b2b;
    --rule: #555555;
    --yellow: #f5b800;
    --orange: #f39a00;
    --green: #22b14c;
    --red: #c0140c;
    --deep-red: #b4100a;
  }
  * { box-sizing: border-box; margin: 0; padding: 0; }
  html, body {
    width: 1200px; height: 900px; overflow: hidden;
    background: var(--backdrop);
    font-family: "Open Sans", Arial, sans-serif;
    color: var(--ink);
  }
  .canvas { position: relative; width: 1200px; height: 900px; }
  .card {
    position: absolute; top: 170px; width: 347px; height: 561px;
    background: var(--card); text-align: center;
  }
  .card--residential { left: 259px; }
  .card--corporate { left: 629px; }
  .free-call { position: absolute; top: 211px; left: 0; right: 0; font-size: 21px; font-weight: 600; line-height: 28px; }
  .card .free-call { top: 41px; }
  .free-call__number { display: block; }
  .website { position: absolute; top: 124px; left: 0; right: 0; font-size: 17px; }
  .brand {
    position: absolute; top: 250px; left: 0; right: 0;
    display: flex; align-items: center; justify-content: center; gap: 10px;
    font-size: 26px; font-weight: 700; text-transform: uppercase; letter-spacing: 0.5px;
  }
  .brand__mark { width: 16px; height: 16px; }
  .card--residential .brand { color: var(--green); }
  .card--residential .brand__mark { background: var(--yellow); }
  .card--corporate .brand { color: var(--red); }
  .card--corporate .brand__mark { background: var(--green); border-radius: 50%; }
  .services-heading {
    position: absolute; top: 382px; left: 42px; right: 62px;
    display: flex; align-items: center; gap: 6px;
    font-size: 21px; font-weight: 400; color: #3a3a3a;
  }
  .services-heading::before, .services-heading::after {
    content: ""; flex: 1; height: 1px; background: var(--rule);
  }
  .services { position: absolute; top: 423px; left: 0; right: 0; list-style: none; font-size: 18.5px; line-height: 29.5px; color: #333; }
  .card--corporate .services { top: 425px; }
  .band { position: absolute; left: 0; right: 0; bottom: 0; height: 20px; }
  .card--residential .band { background: var(--green); }
  .card--corporate .band { background: var(--red); }
  .tone-yellow { color: var(--yellow); }
  .tone-orange { color: var(--orange); }
  .tone-green { color: var(--green); }
  .tone-red { color: var(--deep-red); }
</style>
</head>
<body>
<main class="canvas">
  <section class="card card--residential" aria-label="Residential business card">
    <p class="free-call">Free Call
      <span class="free-call__number">1800 <span class="tone-yellow">L</span><span class="tone-orange">B</span> <span class="tone-green">Cart</span> / 1800 52 41 87</span>
    </p>
    <p class="website">www.larkbendcarters.com.au</p>
    <div class="brand"><span class="brand__mark"></span>Larkbend Carters</div>
    <h2 class="services-heading">SERVICES</h2>
    <ul class="services">
      <li>Local, Country, Interstate</li>
      <li>Furniture Removals</li>
      <li>Piano, Billiard Tables &amp; Antiques</li>
    </ul>
    <div class="band"></div>
  </section>

  <section class="card card--corporate" aria-label="Corporate business card">
    <p class="free-call">Free Call
      <span class="free-call__number">1800 <span class="tone-red">LB Cart</span> / 1800 52 41 87</span>
    </p>
    <p class="website">www.larkbendcarters.com.au</p>
    <div class="brand"><span class="brand__mark"></span>Larkbend Carters</div>
    <h2 class="services-heading">SERVICES</h2>
    <ul class="services">
      <li>Corporate relocations</li>
      <li>Office equipment moves</li>
      <li>Packing Service | Packing Materials</li>
    </ul>
    <div class="band"></div>
  </section>
</main>
</body>
</html>
```